Business Card Design

Business Card for professional consulting firm working with large financial institutions.

Target Market(s)

Executive buyers

Industry/Entity Type

Banking

Contact Information for Business Card

Mild creativity wanted. Not boring, but do elaborate artwork.

Font styles to use
Serif
Sans Serif

Colors

Designer to choose colors to be used in the design.

Requirements
Must have
• Standard business card features - company name, individual name, telephone, website, email, locations.
Nice to have
• Two colors
Should not have
• too many colors, fancy printing, cartoons.

```html
<!DOCTYPE html>
<html lang="en">
<head>
<meta charset="utf-8">
<title>Kestrel Advisory – Business Card</title>
<link rel="stylesheet" href="https://fonts.googleapis.com/css2?family=Montserrat:wght@400;500;600;700&display=swap">
<style>
  :root {
    --stage: #3a3a3c;
    --ink: #1a1a1a;
    --card-dark: #161616;
    --card-light: #ffffff;
    --grey: #b9b9b9;
    --grey-soft: #d4d4d4;
    --text: #2b2b2b;
    --muted: #555555;
  }
  * { box-sizing: border-box; margin: 0; padding: 0; }
  html, body { width: 1200px; height: 1000px; overflow: hidden; }
  body {
    background: var(--stage);
    font-family: "Montserrat", sans-serif;
    position: relative;
  }
  .card {
    position: absolute;
    left: 285px;
    width: 630px;
    height: 360px;
    border-radius: 22px;
    overflow: hidden;
  }
  .card--back { top: 120px; background: var(--card-dark); }
  .card--front { top: 520px; background: var(--card-light); }

  .brand {
    position: absolute;
    font-family: "Montserrat", sans-serif;
    font-weight: 500;
    letter-spacing: 0.5px;
    white-space: nowrap;
  }
  .card--back .brand {
    left: 0; right: 0; top: 150px;
    text-align: center;
    font-size: 46px;
    color: var(--card-light);
  }
  .card--front .brand {
    right: 40px; top: 58px;
    font-size: 34px;
    color: var(--ink);
  }

  .person { position: absolute; left: 40px; top: 84px; }
  .person__name {
    font-weight: 700; font-size: 20px; letter-spacing: 1px; color: var(--text);
  }
  .person__title {
    font-weight: 500; font-size: 11px; letter-spacing: 1px; color: var(--muted); margin-top: 2px;
  }
  .rule {
    position: absolute; height: 1.5px; background: var(--ink);
  }
  .rule--name { left: 40px; right: 40px; top: 134px; }
  .rule--contact { left: 380px; right: 40px; top: 258px; }

  .address {
    position: absolute; left: 40px; top: 148px;
    font-weight: 600; font-size: 13px; line-height: 1.45; color: var(--text);
  }

  .contacts {
    position: absolute; right: 40px; top: 266px;
    list-style: none;
  }
  .contacts li {
    display: flex; align-items: center; justify-content: flex-end; gap: 8px;
    font-weight: 600; font-size: 13px; line-height: 21px; color: var(--text);
  }
  .contacts svg { width: 13px; height: 13px; }

  .base-band {
    position: absolute; left: 0; bottom: 0; width: 630px; height: 48px;
  }
</style>
</head>
<body>

  <section class="card card--back" aria-label="Card back">
    <div class="brand">Kestrel Advisory</div>
  </section>

  <section class="card card--front" aria-label="Card front">
    <div class="brand">Kestrel Advisory</div>

    <div class="person">
      <div class="person__name">DANIEL REYES</div>
      <div class="person__title">GENERAL MANAGER</div>
    </div>
    <div class="rule rule--name"></div>

    <address class="address" style="font-style:normal">
      410 W Harbor Street Meridian Plaza Tower<br>
      12th Floor Portland,<br>
      Oregon 97204
    </address>

    <div class="rule rule--contact"></div>
    <ul class="contacts">
      <li>+503-555-0148
        <svg viewBox="0 0 16 16" aria-hidden="true"><path fill="#9a9a9a" d="M4 1.5l2 3-1.3 1.4a9 9 0 0 0 5.4 5.4L11.5 10l3 2-1 2.5c-6.5 0-12-5.5-12-12z"/></svg>
      </li>
      <li>info@kestreladvisory.us
        <svg viewBox="0 0 16 16" aria-hidden="true"><rect x="1.5" y="3.5" width="13" height="9" fill="none" stroke="#9a9a9a" stroke-width="1.5"/><path d="M1.5 3.5l6.5 5 6.5-5" fill="none" stroke="#9a9a9a" stroke-width="1.5"/></svg>
      </li>
      <li>www.kestreladvisory.us
        <svg viewBox="0 0 16 16" aria-hidden="true"><circle cx="8" cy="8" r="6.5" fill="none" stroke="#9a9a9a" stroke-width="1.4"/><path d="M1.5 8h13M8 1.5c-3 3.5-3 9.5 0 13M8 1.5c3 3.5 3 9.5 0 13" fill="none" stroke="#9a9a9a" stroke-width="1.1"/></svg>
      </li>
    </ul>

    <svg class="base-band" viewBox="0 0 630 48" aria-hidden="true">
      <path d="M0 8 H290 C305 8 305 26 320 26 H630 V48 H0 Z" fill="var(--grey-soft)"/>
      <path d="M0 16 H280 C296 16 296 36 312 36 H330 V48 H0 Z" fill="var(--card-dark)"/>
    </svg>
  </section>

</body>
</html>
```